Dovecote Realty

Business cards for 4 people

They need to say for all
87 Tarrow Quay, Boston MA 02114

Each person will have their own personal information
We would like gold embossing for the name of the company
Marla is the blonde sitting in the chair smiling her information should be on the back of the card with her name and information
Should say for slogan classic pattern, elevated experience
grace@dovecoteprops.com
(413) 555-0182

Odette is the brunette with wavy hair in the tan suit odette@dovecoteprops.com
(617) 555-0137

faith@dovecoteprops.com
(413) 555-0164
standing next to the chair

hope@dovecoteprops.com
(413) 555-0199
close up headshot

```html
<!DOCTYPE html>
<html lang="en">
<head>
<meta charset="utf-8">
<title>Dovecote Realty – Business Cards</title>
<link rel="stylesheet" href="https://fonts.googleapis.com/css2?family=Open+Sans:wght@400;600;700&display=swap">
<style>
  :root {
    --backdrop: #232323;
    --card-dark: #222226;
    --gold: #eebd67;
    --gold-deep: #d9a348;
    --ink-light: #f2f2f2;
    --photo-warm: #8a6242;
    --photo-dark: #2c2a2c;
  }
  * { box-sizing: border-box; margin: 0; padding: 0; }
  html, body {
    width: 1200px; height: 780px; overflow: hidden;
    background: var(--backdrop);
    font-family: "Open Sans", sans-serif;
  }
  .canvas {
    position: relative; width: 1200px; height: 780px;
    display: flex; align-items: center; justify-content: center; gap: 40px;
  }
  .card {
    position: relative; width: 540px; height: 309px;
    border-radius: 3px; overflow: hidden;
    box-shadow: 0 18px 40px rgba(0,0,0,.45);
  }

  /* Back of card: personal details */
  .card--back { background: var(--card-dark); }
  .portrait {
    position: absolute; left: 0; top: 0; width: 250px; height: 270px;
    background: radial-gradient(ellipse at 55% 45%, #a9825c 0%, var(--photo-warm) 40%, var(--photo-dark) 85%);
  }
  .brand {
    position: absolute; right: 34px; top: 26px;
    display: flex; align-items: center; gap: 12px;
  }
  .brand__name {
    color: var(--gold); font-weight: 600; letter-spacing: .08em;
    font-size: 17px; line-height: 1.15; text-align: right; text-transform: uppercase;
  }
  .brand__mark {
    width: 56px; height: 56px; border-radius: 50%;
    border: 2px solid var(--gold);
  }
  .details {
    position: absolute; right: 34px; top: 108px; text-align: right;
    color: var(--ink-light);
  }
  .details__name {
    color: var(--gold); font-weight: 700; font-size: 24px; line-height: 1.1;
  }
  .details__title { font-size: 10.5px; margin-top: 3px; }
  .details__address { font-size: 13px; line-height: 1.35; margin-top: 10px; }
  .contact { list-style: none; margin-top: 10px; font-size: 13px; line-height: 1.55; }
  .contact li { display: flex; align-items: center; justify-content: flex-end; gap: 8px; }
  .contact svg { width: 12px; height: 12px; fill: none; stroke: var(--gold); stroke-width: 1.6; }
  .accent-bar {
    position: absolute; right: 0; top: 112px; width: 16px; height: 26px;
    background: var(--gold);
  }

  /* Front of card: embossed company name */
  .card--front {
    background: linear-gradient(135deg, #f1c16c 0%, var(--gold) 50%, #e8b45c 100%);
    display: flex; align-items: center; justify-content: center; gap: 22px;
  }
  .emboss__name {
    color: var(--gold-deep); font-weight: 600; letter-spacing: .1em;
    font-size: 34px; line-height: 1.15; text-transform: uppercase; text-align: right;
  }
  .emboss__mark {
    width: 96px; height: 96px; border-radius: 50%;
    border: 3px solid var(--gold-deep);
  }
</style>
</head>
<body>
<main class="canvas">
  <section class="card card--back" aria-label="Business card back, Odette Lamberton">
    <div class="portrait" role="img" aria-label="Portrait of Odette, brunette with wavy hair in a tan suit"></div>
    <div class="brand">
      <div class="brand__name">Dovecote<br>Realty</div>
      <div class="brand__mark"></div>
    </div>
    <div class="accent-bar"></div>
    <div class="details">
      <div class="details__name">Odette Lamberton</div>
      <div class="details__title">Real Estate Advisor and Sales Manager</div>
      <div class="details__address">87 Tarrow Quay,<br>Boston MA 02114</div>
      <ul class="contact">
        <li>(617) 555-0137
          <svg viewBox="0 0 12 12"><path d="M2.5 1.5l2 .3.6 2.2-1.2.9a6 6 0 0 0 3.2 3.2l.9-1.2 2.2.6.3 2-1.2 1A8.5 8.5 0 0 1 1.5 2.7z"/></svg>
        </li>
        <li>www.dovecoteprops.com
          <svg viewBox="0 0 12 12"><circle cx="6" cy="6" r="4.8"/><path d="M1.2 6h9.6M6 1.2c-2.6 3-2.6 6.6 0 9.6M6 1.2c2.6 3 2.6 6.6 0 9.6"/></svg>
        </li>
        <li>odette@dovecoteprops.com
          <svg viewBox="0 0 12 12"><rect x="1" y="2.5" width="10" height="7"/><path d="M1 2.5l5 4 5-4"/></svg>
        </li>
      </ul>
    </div>
  </section>

  <section class="card card--front" aria-label="Business card front">
    <div class="emboss__name">Dovecote<br>Realty</div>
    <div class="emboss__mark"></div>
  </section>
</main>
</body>
</html>
```